Jolly Paws Business Card Update

I have a business card which I love. I want to keep the same logo, colours, font and style. I want to upgrade the scripting and remove some elements and add others.
On the front side under Services - remove the existing wording and insert - Providing individual coaching strategies to create happy, healthy and social canine companions
Under Denise Carvell amend the current wording to read: Qualified in Dog Behavioural Training, Natural Animal Healthcare and Animal Health Science
On the reverse side to remove the web address.

```html
<!DOCTYPE html>
<html lang="en">
<head>
<meta charset="utf-8">
<title>Jolly Paws Business Card</title>
<link href="https://fonts.googleapis.com/css2?family=Arimo:wght@400;700&family=Cinzel:wght@500&family=Open+Sans:ital,wght@0,400;0,600;1,400&display=swap" rel="stylesheet">
<style>
  :root {
    --bg: #2b2b2b;
    --blue-deep: #1f3f94;
    --blue-mid: #1d5bb0;
    --blue-light: #0a8fcf;
    --red: #c8161d;
    --red-dark: #7a1518;
    --cream: #efe8d2;
    --white: #ffffff;
    --card-white: #f1f1f1;
    --navy: #273a8c;
    --ink: #111111;
  }
  html, body { margin: 0; padding: 0; }
  body {
    width: 1200px; height: 1138px; overflow: hidden;
    background: var(--bg);
    position: relative;
  }
  .card {
    position: absolute;
    border-radius: 14px;
    overflow: hidden;
  }
  .card-front {
    left: 274px; top: 186px; width: 623px; height: 376px;
    background: linear-gradient(120deg, var(--blue-deep) 0%, var(--blue-mid) 55%, var(--blue-light) 100%);
    color: var(--white);
  }
  .brand-title {
    position: absolute; left: 35px; top: 54px; margin: 0;
    font-family: 'Cinzel', serif; font-weight: 500; font-size: 41px;
    letter-spacing: 0.5px; color: #e6e9f2; line-height: 1;
  }
  .brand-tagline {
    position: absolute; left: 34px; top: 99px; margin: 0;
    font-family: 'Open Sans', sans-serif; font-size: 18px; line-height: 1; color: #e6e9f2;
    letter-spacing: .2px;
  }
  .services-front {
    position: absolute; left: 37px; top: 182px; width: 240px;
    font-family: 'Arimo', sans-serif; font-size: 16px; line-height: 19px; color: #e8ebf4;
  }
  .services-front h2 { margin: 0; font-size: 16px; font-weight: 700; }
  .services-front p { margin: 0; }
  .front-band {
    position: absolute; left: 0; bottom: 0; width: 100%; height: 52px;
    background: linear-gradient(90deg, var(--red-dark) 0%, var(--red) 55%, var(--red-dark) 100%);
    font-family: 'Arimo', sans-serif; font-size: 16.5px; color: #f3e6e6;
    display: flex; align-items: center; justify-content: center;
  }
  .logo-spot {
    position: absolute; display: flex; align-items: center; justify-content: center;
  }
  .logo-spot .dot {
    position: absolute; inset: 0; border-radius: 50%;
    background: var(--cream);
  }
  .logo-spot .logo-name {
    position: relative; font-family: 'Arimo', sans-serif; font-weight: 700;
    color: var(--navy);
  }
  .card-front .logo-spot { left: 328px; top: 38px; width: 260px; height: 260px; }
  .card-front .logo-name { font-size: 30px; }

  .card-back {
    left: 276px; top: 608px; width: 618px; height: 374px;
    background: var(--card-white);
  }
  .back-waves { position: absolute; left: 0; top: 0; }
  .services-back {
    position: absolute; right: 28px; top: 18px; margin: 0;
    text-align: right; font-family: 'Arimo', sans-serif; font-size: 16px; line-height: 19.5px;
    color: var(--white); white-space: nowrap;
  }
  .person { position: absolute; left: 31px; top: 112px; }
  .person-name {
    margin: 0; font-family: 'Open Sans', sans-serif; font-weight: 600; font-size: 25px;
    color: var(--navy); line-height: 1.1;
  }
  .person-quals {
    margin: 3px 0 0; font-family: 'Open Sans', sans-serif; font-style: italic; font-size: 15.5px;
    line-height: 21.5px; color: var(--navy);
  }
  .contact-list {
    position: absolute; left: 31px; top: 247px; margin: 0; padding: 0; list-style: none;
    font-family: 'Open Sans', sans-serif; font-size: 16px; color: var(--navy);
  }
  .contact-list li { display: flex; align-items: center; height: 23px; }
  .contact-list svg { width: 14px; height: 14px; margin-right: 15px; fill: var(--red); }
  .back-footer {
    position: absolute; left: 0; width: 100%; top: 330px; margin: 0; text-align: center;
    font-family: 'Arimo', sans-serif; font-size: 16.5px; color: var(--ink);
  }
  .card-back .logo-spot { left: 404px; top: 128px; width: 184px; height: 184px; }
  .card-back .logo-name { font-size: 23px; }
</style>
</head>
<body>

<section class="card card-front">
  <h1 class="brand-title">JOLLY PAWS</h1>
  <p class="brand-tagline">HAPPY DOGS, HAPPY OWNERS</p>
  <div class="services-front">
    <h2>SERVICES</h2>
    <p>Providing individual coaching strategies to create happy, healthy and social canine companions</p>
  </div>
  <div class="logo-spot">
    <span class="dot"></span>
    <span class="logo-name">Jolly Paws</span>
  </div>
  <div class="front-band">Promoting communication and connection between dogs and their families</div>
</section>

<section class="card card-back">
  <svg class="back-waves" width="618" height="374" viewBox="0 0 618 374" aria-hidden="true">
    <defs>
      <linearGradient id="backBlue" x1="0" y1="0" x2="1" y2="0">
        <stop offset="0" stop-color="#0a8fcf"/>
        <stop offset=".5" stop-color="#1f4fa5"/>
        <stop offset="1" stop-color="#243d92"/>
      </linearGradient>
    </defs>
    <path d="M0,0 H618 V112 C560,128 490,128 440,118 C380,106 340,60 280,40 C190,12 80,28 0,58 Z" fill="url(#backBlue)"/>
    <path d="M0,80 C90,42 200,30 290,52 C360,70 400,112 460,132 C520,148 580,136 618,124 V132 C580,146 520,156 460,142 C400,124 360,84 290,64 C200,42 100,60 0,98 Z" fill="#7a1518"/>
    <path d="M40,100 C130,64 230,58 300,74 C370,90 410,130 470,148 C530,162 580,150 618,140 V144 C580,156 530,168 470,154 C410,138 370,98 300,82 C230,66 130,72 40,100 Z" fill="#c8161d"/>
  </svg>
  <p class="services-back"><strong>SERVICES:</strong> Providing Individual<br>Coaching Strategies to Create<br>Happy, Healthy and Social<br>Canine Companions</p>
  <div class="person">
    <h2 class="person-name">Denise Carvell</h2>
    <p class="person-quals">Qualified in Dog Behavioural Training,<br>Natural Animal Healthcare and<br>Animal Health Science</p>
  </div>
  <ul class="contact-list">
    <li><svg viewBox="0 0 14 14"><path d="M3,0 H11 V14 H3 Z M4.5,2 V8 H9.5 V2 Z M5,9.5 H6.5 V11 H5 Z M7.5,9.5 H9 V11 H7.5 Z" fill-rule="evenodd"/></svg>0400 218 657</li>
    <li><svg viewBox="0 0 14 14"><path d="M0,3 H14 V12 H0 Z M0,3 L7,8 L14,3 V4.5 L7,9.5 L0,4.5 Z" fill-rule="evenodd"/></svg>jollypaws1@mailbox.com</li>
  </ul>
  <div class="logo-spot">
    <span class="dot"></span>
    <span class="logo-name">Jolly Paws</span>
  </div>
  <p class="back-footer">Promoting communication and connection between dogs and their families</p>
</section>

</body>
</html>
```